Veldmark Supplies Business Card

Professional business card that stand out to our potential customers. Front and back with clean modern design

Industry/Entity Type

Oil and gas

Contact Information for Business Card

Name, address, website , office phone and cell number

Requirements
Must have
• Editable files for each employee

```html
<!DOCTYPE html>
<html lang="en">
<head>
<meta charset="utf-8">
<title>Veldmark Supplies – Business Card</title>
<link href="https://fonts.googleapis.com/css2?family=Montserrat:wght@400;500;700&display=swap" rel="stylesheet">
<style>
  :root {
    --stage: #d9d4cc;
    --card-white: #ffffff;
    --brand-red: #e8202a;
    --brand-blue: #00afd0;
    --icon-blue: #1aa6cf;
    --ink: #1f1f1f;
    --shadow: rgba(0, 0, 0, 0.28);
  }
  * { box-sizing: border-box; margin: 0; padding: 0; }
  html, body {
    width: 900px; height: 1200px; overflow: hidden;
    background: var(--stage);
    font-family: "Montserrat", Arial, sans-serif;
  }
  .canvas { position: relative; width: 900px; height: 1200px; }

  .card {
    position: absolute;
    border-radius: 24px;
    box-shadow: 0 10px 22px var(--shadow);
    overflow: hidden;
  }
  .card-front { left: 80px; top: 130px; width: 742px; height: 442px; background: var(--card-white); }
  .card-back  { left: 78px; top: 638px; width: 744px; height: 440px; background: var(--brand-blue); }

  .brand-name {
    display: flex; align-items: center; gap: 10px;
    font-weight: 700; color: var(--brand-red); white-space: nowrap;
  }
  .brand-mark { display: block; background: var(--brand-red); flex: none; }

  .front-brand { position: absolute; left: 35px; top: 190px; font-size: 25px; }
  .front-brand .brand-mark { width: 18px; height: 18px; }

  .feature-brand {
    position: absolute; left: 488px; top: 150px; width: 230px;
    flex-direction: column; align-items: flex-start; gap: 16px;
    font-size: 40px; line-height: 1.1; white-space: normal;
  }
  .feature-brand .brand-mark { width: 56px; height: 56px; }
  .feature-brand .brand-line { display: block; }

  .person { position: absolute; left: 516px; top: 42px; }
  .person-name { font-size: 26px; font-weight: 700; color: var(--brand-red); line-height: 1.2; }
  .person-title { font-size: 16px; font-weight: 500; color: var(--ink); margin-top: 2px; }

  .address {
    position: absolute; left: 35px; top: 236px;
    font-size: 16px; line-height: 21px; color: var(--ink); font-style: normal;
  }
  .contact-list {
    position: absolute; left: 35px; top: 292px; list-style: none;
    font-size: 16px; color: var(--ink);
  }
  .contact-list li { display: flex; align-items: center; gap: 8px; height: 27.5px; }
  .contact-list svg { width: 17px; height: 17px; fill: var(--icon-blue); flex: none; }

  .back-brand {
    position: absolute; left: 0; right: 0; top: 0; bottom: 0;
    justify-content: center; font-size: 46px; color: #ffffff;
  }
  .back-brand .brand-mark { width: 34px; height: 34px; background: #ffffff; }
</style>
</head>
<body>
<main class="canvas">

  <section class="card card-front" aria-label="Business card front">
    <div class="brand-name front-brand"><span class="brand-mark"></span>Veldmark Supplies</div>

    <div class="person">
      <p class="person-name">Tarek Hollins</p>
      <p class="person-title">President</p>
    </div>

    <address class="address">42 Ridgeline Court<br>Ashford, NJ 07815 USA</address>

    <ul class="contact-list">
      <li>
        <svg viewBox="0 0 24 24" aria-hidden="true"><path d="M4 9c0-3 4-5 8-5s8 2 8 5v2h-4V9c-1-1-2.5-1.3-4-1.3S9 8 8 9v2H4z"/><path d="M6 13h12l2 7H4z"/></svg>
        +1.555.210.4400 x123
      </li>
      <li>
        <svg viewBox="0 0 24 24" aria-hidden="true"><path d="M6.6 10.8a15 15 0 0 0 6.6 6.6l2.2-2.2a1 1 0 0 1 1-.25 11.4 11.4 0 0 0 3.6.6 1 1 0 0 1 1 1V20a1 1 0 0 1-1 1A17 17 0 0 1 3 4a1 1 0 0 1 1-1h3.5a1 1 0 0 1 1 1c0 1.25.2 2.45.6 3.6a1 1 0 0 1-.25 1z"/></svg>
        +1.555.318.072
      </li>
      <li>
        <svg viewBox="0 0 24 24" aria-hidden="true"><path d="M3 6h18l-9 7z"/><path d="M3 8l9 7 9-7v10H3z"/></svg>
        info@veldmarksupplies.com
      </li>
      <li>
        <svg viewBox="0 0 24 24" aria-hidden="true"><circle cx="12" cy="12" r="9"/></svg>
        www.veldmarksupplies.com
      </li>
    </ul>

    <div class="brand-name feature-brand">
      <span class="brand-mark"></span>
      <span class="brand-text"><span class="brand-line">Veldmark</span><span class="brand-line">Supplies</span></span>
    </div>
  </section>

  <section class="card card-back" aria-label="Business card back">
    <div class="brand-name back-brand"><span class="brand-mark"></span>Veldmark Supplies</div>
  </section>

</main>
</body>
</html>
```